Sophisticated, clean website reflecting my feminine, playful side to sell my abstract art,

I need a website no more than 3 pages to showcase my paintings, a little about me and some contact info. I do abstracts so looking for something a little edgy, yet feminine and current.
Updates

Hi there, These are some artists websites that I Iike: Marnelvoss.com (I like how airy it is) peterwallombry.com garethpolvens.com (I like how it scrolls) I'll need a place for a photo ( a headshot-i do not have it yet so I'll need to be able to upload that later) as well as an area for my bio. Also, it's important that I will be able to upload any new photos and descriptions easily so it should be user friendly. Lastly, I like in a sunny place so would like to have this seem upbeat and playful as that is how i like to paint. thanks-I'm trying to upload my photos now -

Target Market(s)

ppl ages 35-70 who want large scale art for their homes

Industry/Entity Type

art

Coding

Coded - Design and coding required

Number of Pages Required

3 page

Colors

Designer to choose colors to be used in the design.

Requirements
Must have
• photos of my art, a place for my bio, be easy to reach me. tasteful-nothing too "in your face" -my clients are pretty high end and organized. They like clean lines
Nice to have
• sophisticated background, muted tones in the back-similar clean font throughout-no cursive
Should not have
• too many dark areas. Too many blocks of color. Too serious.

```html
<!DOCTYPE html>
<html lang="en">
<head>
<meta charset="utf-8">
<title>Helena Marsh Art</title>
<link href="https://fonts.googleapis.com/css2?family=Roboto:wght@300;400;500;700&family=Great+Vibes&display=swap" rel="stylesheet">
<style>
:root{
  --header-bg:#f6f4f2;
  --lavender:#f4f0fa;
  --stone:#f0eeec;
  --ink:#1d1b1f;
  --text:#4a474d;
  --muted:#9a979c;
  --pink:#f3c9c2;
  --pink-deep:#eab3ab;
  --frame:#a8652c;
  --frame-dark:#7a4419;
  --line:#dcd8dd;
  --white:#ffffff;
  --art-hero:#b8a9c2;
  --art-ochre:#c9a24a;
  --art-rose:#d8a9a8;
  --art-teal:#5f8a72;
  --art-photo:#a98a78;
}
*{box-sizing:border-box;margin:0;padding:0}
html,body{width:1200px;height:3192px;overflow:hidden}
body{position:relative;font-family:'Roboto',sans-serif;color:var(--ink);background:var(--lavender)}
.abs{position:absolute}
.band{position:absolute;left:0;width:1200px}
.header{top:0;height:84px;background:var(--header-bg)}
.hero{top:84px;height:1496px;background:var(--lavender)}
.about{top:1580px;height:598px;background:var(--lavender)}
.contact{top:2178px;height:652px;background:var(--stone)}
.footer{top:2830px;height:362px;background:var(--lavender)}

.brand{font-family:'Roboto',sans-serif;font-weight:400;color:var(--ink);letter-spacing:.5px;white-space:nowrap}
.nav{top:28px;left:432px;display:flex;gap:30px;font-size:15px;font-weight:500}
.nav a{color:var(--ink);text-decoration:none}
.nav a.active{color:var(--pink-deep)}
.social{width:40px;height:40px;border:1.5px solid #8e8b90;border-radius:50%}
.btn{background:var(--pink);color:var(--white);border-radius:30px;font-weight:500;display:flex;align-items:center;justify-content:center;text-transform:uppercase;font-size:15px}
.script{font-family:'Great Vibes',cursive;font-weight:400;text-align:center;color:var(--ink);white-space:nowrap}

.frame{border:16px solid var(--frame);box-shadow:inset 0 0 0 2px var(--frame-dark),0 2px 4px rgba(0,0,0,.2)}
.art{width:100%;height:100%}
.dots{display:flex;gap:5px}
.dots span{width:10px;height:10px;border:1.5px solid #fff;border-radius:50%}
.dots span.on{background:#fff}

.card-title{font-size:21px;font-weight:500;text-align:center;width:294px}
.card-desc{font-size:13px;color:var(--muted);text-align:center;width:294px}
.card-size{font-size:14px;font-weight:500;color:var(--text);text-align:center;width:294px}

.para{font-size:15px;line-height:26.5px;color:var(--text);text-align:justify}

.field{background:var(--white);border:1px solid var(--line);font-size:12px;color:var(--text);padding:0 16px;display:flex;align-items:center;gap:6px}
.field.tall{align-items:flex-start;padding-top:14px}

.foot-h{font-size:17px;font-weight:500}
.foot-list{list-style:none;font-size:14px;color:var(--text);line-height:26px}
.foot-label{font-size:11px;color:var(--pink-deep)}
.foot-val{font-size:14px;color:var(--text);line-height:18px}
.copy{font-size:15px;color:var(--text);text-align:center;width:1200px}
.ficon{width:32px;height:32px;border:1.5px solid #b8b4ba;border-radius:50%}
</style>
</head>
<body>

<div class="band header"></div>
<div class="band hero"></div>
<div class="band about"></div>
<div class="band contact"></div>
<div class="band footer"></div>

<!-- Header -->
<div class="abs brand" style="left:112px;top:26px;font-size:24px">Helena Marsh Art</div>
<nav class="abs nav">
  <a class="active" href="#">Home</a>
  <a href="#">About Me</a>
  <a href="#">My Paintings</a>
  <a href="#">Contact Us</a>
</nav>
<div class="abs social" style="left:849px;top:17px" aria-label="Social profile"></div>
<div class="abs social" style="left:899px;top:17px" aria-label="Social profile"></div>
<div class="abs btn" style="left:960px;top:20px;width:128px;height:36px;text-transform:none;font-size:15px">Subscribe</div>

<!-- Hero -->
<h1 class="abs brand" style="left:0;width:1200px;top:124px;text-align:center;font-size:62px;font-weight:300">Helena Marsh Art</h1>
<div class="abs frame" style="left:171px;top:251px;width:858px;height:558px">
  <div class="art" role="img" aria-label="Featured abstract painting in purple and blue tones" style="background:linear-gradient(180deg,#c7bccd,var(--art-hero))"></div>
</div>
<div class="abs dots" style="left:568px;top:794px"><span></span><span></span><span class="on"></span><span></span><span></span></div>

<!-- Paintings -->
<h2 class="abs script" style="left:0;width:1200px;top:890px;font-size:84px">My Paintings</h2>

<div class="abs frame" style="left:112px;top:1032px;width:294px;height:392px">
  <div class="art" role="img" aria-label="Abstract painting in ochre, red and navy" style="background:var(--art-ochre)"></div>
</div>
<div class="abs card-title" style="left:112px;top:1445px">Artwork 1</div>
<div class="abs card-desc" style="left:112px;top:1472px">Lorem ipsum dolor sit</div>
<div class="abs card-size" style="left:112px;top:1503px">48" X 60"</div>

<div class="abs frame" style="left:453px;top:1032px;width:294px;height:392px">
  <div class="art" role="img" aria-label="Abstract floral painting in pink and plum" style="background:var(--art-rose)"></div>
</div>
<div class="abs card-title" style="left:453px;top:1445px">Artwork 1</div>
<div class="abs card-desc" style="left:453px;top:1472px">Lorem ipsum dolor sit</div>
<div class="abs card-size" style="left:453px;top:1503px">48" X 60"</div>

<div class="abs frame" style="left:793px;top:1032px;width:294px;height:392px">
  <div class="art" role="img" aria-label="Abstract painting in teal, green and black" style="background:var(--art-teal)"></div>
</div>
<div class="abs card-title" style="left:793px;top:1445px">Artwork 1</div>
<div class="abs card-desc" style="left:793px;top:1472px">Lorem ipsum dolor sit</div>
<div class="abs card-size" style="left:793px;top:1503px">48" X 60"</div>

<!-- About -->
<div class="abs" style="left:120px;top:1670px;width:452px;height:452px;border-radius:50%;background:var(--pink)"></div>
<div class="abs" role="img" aria-label="Photo of the artist at work in her studio" style="left:112px;top:1670px;width:446px;height:446px;border-radius:50%;background:var(--art-photo)"></div>

<h2 class="abs script" style="left:647px;top:1690px;font-size:84px;text-align:left">About Me</h2>
<p class="abs para" style="left:647px;top:1800px;width:441px">Lorem ipsum dolor sit amet, consectetur adipiscing elit, sed do eiusmod tempor incididunt ut labore et dolore magna aliqua. Ut enim ad minim veniam, quis nostrud exercitation ullamco laboris nisi ut aliquip ex ea commodo consequat.</p>
<p class="abs para" style="left:647px;top:1918px;width:441px">Duis aute irure dolor in reprehenderit in voluptate velit esse cillum dolore eu fugiat nulla pariatur. Excepteur sint occaecat cupidatat non qui officia deserunt mollit anim id est laborum.</p>
<div class="abs btn" style="left:647px;top:2030px;width:174px;height:50px;gap:8px">Learn More
  <svg width="14" height="14" viewBox="0 0 14 14"><circle cx="7" cy="7" r="7" fill="#fff"/><path d="M5.5 4 L8.5 7 L5.5 10" stroke="#f3c9c2" stroke-width="1.8" fill="none"/></svg>
</div>

<!-- Contact -->
<h2 class="abs script" style="left:0;width:1200px;top:2250px;font-size:84px">Contact Us</h2>
<div class="abs field" style="left:110px;top:2411px;width:223px;height:44px">
  <svg width="11" height="11" viewBox="0 0 12 12"><circle cx="6" cy="4" r="2.5" fill="none" stroke="#666"/><path d="M1.5 11.5 Q6 6 10.5 11.5" fill="none" stroke="#666"/></svg>Name</div>
<div class="abs field" style="left:348px;top:2411px;width:223px;height:44px">
  <svg width="11" height="11" viewBox="0 0 12 12"><path d="M2 1 L4.5 1 L5.5 4 L4 5 Q5 7.5 7 8 L8 6.5 L11 7.5 L11 10 Q6 11.5 1 2 Z" fill="#666"/></svg>Phone Number</div>
<div class="abs field" style="left:110px;top:2469px;width:223px;height:44px">
  <svg width="12" height="10" viewBox="0 0 12 10"><rect x=".5" y=".5" width="11" height="9" fill="none" stroke="#666"/><path d="M.5 .5 L6 5 L11.5 .5" fill="none" stroke="#666"/></svg>Email Address</div>
<div class="abs field" style="left:348px;top:2469px;width:223px;height:44px">
  <svg width="11" height="11" viewBox="0 0 12 12"><path d="M1 11 L2 8 L8.5 1.5 L10.5 3.5 L4 10 Z" fill="#666"/></svg>Subject</div>
<div class="abs field tall" style="left:110px;top:2526px;width:461px;height:86px">
  <svg width="12" height="11" viewBox="0 0 12 11"><ellipse cx="6" cy="5" rx="5.5" ry="4" fill="none" stroke="#666"/><path d="M3 8.5 L2 10.5 L5 9" fill="none" stroke="#666"/></svg>Messagge</div>
<div class="abs btn" style="left:112px;top:2643px;width:140px;height:42px">Submit</div>

<div class="abs" role="img" aria-label="Detail of a green and teal abstract painting" style="left:634px;top:2360px;width:446px;height:340px;background:var(--art-teal)"></div>

<!-- Footer -->
<div class="abs brand" style="left:115px;top:2940px;font-size:24px">Helena Marsh Art</div>
<div class="abs ficon" style="left:155px;top:2987px" aria-label="Social profile"></div>
<div class="abs ficon" style="left:196px;top:2987px" aria-label="Social profile"></div>
<div class="abs ficon" style="left:236px;top:2987px" aria-label="Social profile"></div>
<div class="abs ficon" style="left:277px;top:2987px" aria-label="Social profile"></div>

<div class="abs foot-h" style="left:431px;top:2888px">Quick Links</div>
<ul class="abs foot-list" style="left:431px;top:2928px">
  <li>Home</li><li>About Me</li><li>My Paintings</li><li>Contact Us</li>
</ul>

<div class="abs foot-h" style="left:622px;top:2888px">About Company</div>
<ul class="abs foot-list" style="left:622px;top:2928px">
  <li>Legal Information</li><li>Terms &amp; Condition</li><li>Privacy Policy</li><li>Support</li><li>Site Map</li>
</ul>

<div class="abs foot-h" style="left:850px;top:2888px">Contact Us</div>
<svg class="abs" style="left:849px;top:2932px" width="13" height="13" viewBox="0 0 12 12"><path d="M2 1 L4.5 1 L5.5 4 L4 5 Q5 7.5 7 8 L8 6.5 L11 7.5 L11 10 Q6 11.5 1 2 Z" fill="#eab3ab"/></svg>
<div class="abs foot-label" style="left:872px;top:2932px">Phone</div>
<div class="abs foot-val" style="left:872px;top:2952px">+1 888 888 8888</div>
<svg class="abs" style="left:846px;top:2984px" width="14" height="11" viewBox="0 0 14 11"><rect width="14" height="11" fill="#eab3ab"/><path d="M0 0 L7 6 L14 0" stroke="#fff" fill="none"/></svg>
<div class="abs foot-label" style="left:872px;top:2983px">Email</div>
<div class="abs foot-val" style="left:872px;top:3004px">studio@helenamarshart.com</div>
<svg class="abs" style="left:849px;top:3034px" width="10" height="14" viewBox="0 0 10 14"><path d="M5 14 Q0 7 0 5 A5 5 0 0 1 10 5 Q10 7 5 14 Z" fill="#eab3ab"/><circle cx="5" cy="5" r="1.8" fill="#fff"/></svg>
<div class="abs foot-label" style="left:872px;top:3034px">Location</div>
<div class="abs foot-val" style="left:872px;top:3055px;width:220px">8020 Lorem ipsum dolor sit amet, consectetur adipiscing elit,</div>

<div class="abs" style="left:108px;top:3124px;width:984px;height:1px;background:var(--line)"></div>
<div class="abs copy" style="left:0;top:3148px">2022 Copyright -&nbsp;&nbsp;Helena Marsh Art&nbsp;&nbsp;&nbsp;|&nbsp;&nbsp;&nbsp;All Rights Reserved</div>

<div class="abs" style="left:1106px;top:3104px;width:36px;height:36px;border-radius:50%;background:var(--pink)">
  <svg width="36" height="36" viewBox="0 0 36 36"><path d="M12 21 L18 15 L24 21" stroke="#fff" stroke-width="2" fill="none"/></svg>
</div>

</body>
</html>
```